Website Design for Landscaping/Concrete Company

I need a website that is informative about what my company does and also offers before and after pictures of completed work. I already have a logo. The website must say "FREE ESTIMATES" somewhere and list a phone number. I would like to stick with the logo colors or similar (black and lime green).
Services Offered by Tomlet Builders:
Landscaping
Mowing
Concrete
Sidewalks
Brush Removal
Land Beautification

Please list the company name in large letters TOMLET BUILDERS
and also the contact information in large font.

Right now I am looking for a somewhat coverpage for my website. I don't have a lot of information for people to point and click on yet. Id like to get a coverpage to get my name out and then have a designer come back in a few months and update with more pictures and information.
Updates

If allowed please submit projects after due date. I made a mistake and only posted for one day. Thanks.

Coding

Coded - Design and coding required

```html
<!DOCTYPE html>
<html lang="en">
<head>
<meta charset="utf-8">
<title>Tomlet Builders</title>
<link rel="stylesheet" href="https://fonts.googleapis.com/css2?family=Montserrat:wght@500;600;700&family=Open+Sans:wght@400;600;700&display=swap">
<style>
:root{
  --lime:#8cb512;
  --lime-light:#a9cf2a;
  --lime-dark:#6f9408;
  --black:#0d0d0d;
  --ink:#222;
  --muted:#666;
  --grey-bg:#f1f1f1;
  --white:#fff;
}
*{box-sizing:border-box;margin:0;padding:0}
html,body{width:1200px;height:4156px;overflow:hidden;background:var(--white)}
body{position:relative;font-family:"Open Sans",Arial,sans-serif;color:var(--ink)}
.abs{position:absolute}
h1,h2,h3,h4,.brand,.nav a,.btn{font-family:"Montserrat",Arial,sans-serif}

/* hero */
.hero{left:0;top:0;width:1200px;height:820px;background:linear-gradient(180deg,#6f95b8 0%,#9fb9c9 18%,#4e7a36 42%,#6f9a3c 62%,#8e9a88 78%,#b7b3a6 100%)}
.hero-shade{left:0;top:0;width:1200px;height:150px;background:linear-gradient(180deg,rgba(0,0,0,.55),rgba(0,0,0,0))}
.brand-block{left:160px;top:14px;display:flex;align-items:center;gap:12px}
.brand-mark{width:34px;height:34px;background:var(--lime)}
.brand{color:var(--lime);font-weight:700;font-size:22px;letter-spacing:1px;line-height:1}
.contact-top{top:14px;display:flex;align-items:center;gap:10px;color:var(--white);font-size:13px;line-height:1.3}
.contact-top b{font-weight:700}
.icon-circle{width:36px;height:36px;border-radius:50%;background:var(--lime);display:flex;align-items:center;justify-content:center}
.nav{left:462px;top:96px;height:34px;display:flex;background:rgba(0,0,0,.8)}
.nav a{display:block;padding:0 16px;line-height:34px;color:var(--white);font-size:12px;font-weight:700;text-decoration:none;letter-spacing:.5px}
.nav a.active{background:var(--lime)}
.hero-title{left:0;width:1200px;top:200px;text-align:center;color:var(--white);font-size:58px;font-weight:700;letter-spacing:3px;text-shadow:0 2px 8px rgba(0,0,0,.4)}
.btn-estimate{left:468px;top:286px;width:264px;height:58px;background:rgba(20,20,20,.85);border:2px solid var(--white);color:var(--white);font-size:22px;font-weight:600;text-align:center;line-height:54px;letter-spacing:1px}

/* welcome */
.welcome-photo-frame{left:200px;top:930px;width:250px;height:310px;border:4px solid var(--lime)}
.welcome-photo{left:172px;top:902px;width:250px;height:310px;background:linear-gradient(180deg,#6e9ec7 0%,#5d8a3a 35%,#8f8052 65%,#b07a4e 100%)}
.welcome-text{left:548px;top:930px;width:470px}
.welcome-head{display:flex;align-items:center;gap:14px;margin-bottom:22px}
.sq{width:38px;height:38px;background:var(--black)}
.welcome-head small{display:block;font-size:16px;color:var(--ink)}
.welcome-head h2{font-size:26px;color:var(--lime);font-weight:700;letter-spacing:.5px}
.body-copy{font-size:12px;line-height:1.75;color:var(--muted);margin-bottom:16px}
.btn-green{display:inline-block;background:var(--lime);color:var(--white);font-family:"Montserrat",sans-serif;font-size:14px;font-weight:700;padding:12px 24px;margin-top:8px}

/* services */
.services-band{left:0;top:1360px;width:1200px;height:420px}
.services-head{left:200px;top:1420px;width:800px;text-align:center;color:var(--white)}
.services-head small{display:block;font-size:16px}
.services-head h2{font-size:28px;font-weight:700;letter-spacing:.5px;margin:4px 0 18px}
.services-head p{font-size:13px;line-height:1.7}
.service{width:210px}
.service h3{font-size:18px;color:var(--lime);font-weight:700;margin-bottom:6px;letter-spacing:.3px}
.service p{font-size:11px;line-height:1.5;color:var(--muted)}
.service.left{text-align:right}
.hub-name{left:450px;top:1935px;width:300px;text-align:center;color:var(--lime);font-family:"Montserrat",sans-serif;font-weight:700;font-size:30px;line-height:1.15}

/* gallery */
.gallery-head{left:172px;top:2260px;display:flex;align-items:center;gap:14px}
.gallery-head small{display:block;font-size:16px}
.gallery-head h2{font-size:26px;color:var(--lime);font-weight:700}
.photo{position:absolute}

/* features */
.features{left:0;top:2880px;width:1200px;height:760px;background:var(--grey-bg)}
.features-head{left:0;top:2952px;width:1200px;text-align:center}
.features-head small{display:block;font-size:16px}
.features-head h2{font-size:28px;color:var(--lime);font-weight:700;margin-top:4px}
.card{width:420px;height:200px;padding:40px 44px;box-shadow:0 3px 10px rgba(0,0,0,.12)}
.card h4{font-size:15px;font-weight:700;margin-bottom:10px;letter-spacing:.3px}
.card p{font-size:12px;line-height:1.6}
.card.plain{background:var(--white)}
.card.plain p{color:var(--muted)}
.card.green{background:linear-gradient(180deg,var(--lime-dark),var(--lime-light));color:var(--white)}
.card-icon{width:34px;height:34px;border:2px solid currentColor;border-radius:50%;margin-bottom:12px}

/* footer */
.footer{left:0;top:3560px;width:1200px;height:596px}
.footer-brand{left:180px;top:3740px;display:flex;flex-direction:column;align-items:center;gap:12px}
.footer-brand .brand-mark{width:64px;height:64px}
.footer-brand .brand{font-size:26px;text-align:center}
.footer-col{top:3730px;color:var(--white)}
.footer-col h3{font-size:22px;font-weight:600;letter-spacing:1px;padding-bottom:10px;border-bottom:2px solid var(--lime);margin-bottom:24px;width:200px}
.footer-col li{list-style:none;font-size:13px;line-height:2}
.footer-contact{display:flex;align-items:center;gap:12px;margin-bottom:22px;font-size:13px;line-height:1.4}
.footer-rule{left:170px;top:4040px;width:860px;height:1px;background:#444}
.copyright{left:0;top:4066px;width:1200px;text-align:center;color:#bbb;font-size:12px}
</style>
</head>
<body>

<!-- HERO -->
<div class="abs hero" role="img" aria-label="Photo of a landscaped garden patio with outdoor furniture, lawn and flower beds"></div>
<div class="abs hero-shade"></div>
<div class="abs brand-block"><span class="brand-mark"></span><span class="brand">TOMLET<br>BUILDERS</span></div>
<div class="abs contact-top" style="left:540px">
  <span class="icon-circle"><svg width="18" height="18" viewBox="0 0 24 24"><path fill="#fff" d="M6.6 10.8a15 15 0 0 0 6.6 6.6l2.2-2.2c.3-.3.7-.4 1-.2 1.1.4 2.3.6 3.6.6.6 0 1 .4 1 1V20c0 .6-.4 1-1 1A17 17 0 0 1 3 4c0-.6.4-1 1-1h3.5c.6 0 1 .4 1 1 0 1.3.2 2.5.6 3.6.1.3 0 .7-.2 1z"/></svg></span>
  <span>Call Us At:<br><b>+1 555 014 2290</b></span>
</div>
<div class="abs contact-top" style="left:770px">
  <span class="icon-circle"><svg width="18" height="18" viewBox="0 0 24 24"><path fill="#fff" d="M3 5h18v14H3z"/><path fill="none" stroke="#8cb512" stroke-width="2" d="M3 6l9 7 9-7"/></svg></span>
  <span>Email Us At:<br><b>info@tomletbuilders.com</b></span>
</div>
<nav class="abs nav">
  <a class="active">HOME</a><a>ABOUT US</a><a>SERVICES</a><a>PORTFOLIO</a><a>FEATURES</a><a>CONTACT US</a>
</nav>
<h1 class="abs hero-title">TOMLET BUILDERS</h1>
<div class="abs btn btn-estimate">FREE ESTIMATES</div>
<svg class="abs" style="left:0;top:700px" width="1200" height="130" viewBox="0 0 1200 130"><polygon points="0,120 600,40 1200,120 1200,130 0,130" fill="#fff"/></svg>

<!-- WELCOME -->
<div class="abs welcome-photo-frame"></div>
<div class="abs welcome-photo" role="img" aria-label="Photo of a garden with brick paving and planted borders"></div>
<div class="abs welcome-text">
  <div class="welcome-head"><span class="sq"></span><div><small>Welcome to</small><h2>TOMLET BUILDERS</h2></div></div>
  <p class="body-copy">We shape outdoor spaces with care, from fresh lawns and planted borders to solid concrete paths and patios. Every project is planned with you and finished on time, with a clean site left behind.</p>
  <p class="body-copy">Our crew brings years of local experience in landscaping and concrete work. We use quality materials, honest pricing and clear communication so your yard looks great for years to come.</p>
  <span class="btn-green">READ MORE</span>
</div>

<!-- SERVICES -->
<svg class="abs services-band" viewBox="0 0 1200 420" preserveAspectRatio="none">
  <defs><linearGradient id="bandGrad" x1="0" y1="0" x2="0" y2="1"><stop offset="0" stop-color="#739a08"/><stop offset="1" stop-color="#b3d735"/></linearGradient></defs>
  <polygon points="0,0 1200,0 1200,330 600,420 0,330" fill="url(#bandGrad)"/>
</svg>
<div class="abs services-head">
  <small>Our</small>
  <h2>TOMLET BUILDERS SERVICES</h2>
  <p>From weekly mowing to new sidewalks, we handle the work that keeps your property neat, safe and welcoming. Call today to book a visit and get a clear quote for your project with no cost or obligation.</p>
</div>

<svg class="abs" style="left:0;top:1650px" width="1200" height="600" viewBox="0 0 1200 600">
  <g fill="none" stroke="#222" stroke-width="2">
    <path d="M380 100 H440 Q470 100 480 140"/>
    <path d="M380 210 H420"/>
    <path d="M380 320 H440 Q470 320 480 290"/>
    <path d="M820 100 H760 Q730 100 720 140"/>
    <path d="M820 210 H780"/>
    <path d="M820 320 H760 Q730 320 720 290"/>
  </g>
  <circle cx="600" cy="215" r="180" fill="#8cb512"/>
  <circle cx="600" cy="215" r="168" fill="#0d0d0d"/>
  <circle cx="600" cy="395" r="16" fill="#8cb512"/>
  <g>
    <circle cx="370" cy="100" r="28" fill="#8cb512"/><circle cx="370" cy="210" r="28" fill="#0d0d0d"/><circle cx="370" cy="320" r="28" fill="#8cb512"/>
    <circle cx="830" cy="100" r="28" fill="#8cb512"/><circle cx="830" cy="210" r="28" fill="#0d0d0d"/><circle cx="830" cy="320" r="28" fill="#8cb512"/>
  </g>
  <g fill="none" stroke="#fff" stroke-width="2.5" stroke-linecap="round">
    <path d="M360 110 L370 88 L380 110 M370 110 V116"/>
    <path d="M358 216 H382 M362 204 H378 L374 216"/>
    <path d="M358 314 H382 V326 H358 Z"/>
    <path d="M820 112 L828 88 M832 112 L840 88"/>
    <path d="M822 200 H838 L836 222 H824 Z M818 200 H842"/>
    <path d="M830 332 V314 M830 318 Q820 308 822 302 Q832 304 830 318 Q840 306 840 302"/>
  </g>
</svg>
<div class="abs hub-name">TOMLET<br>BUILDERS</div>
<div class="abs service left" style="left:130px;top:1722px"><h3>LANDSCAPING</h3><p>Neat, reliable work done right for every yard.</p></div>
<div class="abs service left" style="left:130px;top:1832px"><h3>MOWING</h3><p>Neat, reliable work done right for every yard.</p></div>
<div class="abs service left" style="left:130px;top:1942px"><h3>CONCRETE</h3><p>Neat, reliable work done right for every yard.</p></div>
<div class="abs service" style="left:860px;top:1722px"><h3>SIDEWALKS</h3><p>Neat, reliable work done right for every yard.</p></div>
<div class="abs service" style="left:860px;top:1832px"><h3>BRUSH REMOVAL</h3><p>Neat, reliable work done right for every yard.</p></div>
<div class="abs service" style="left:860px;top:1942px"><h3>LAND BEAUTIFICATION</h3><p>Neat, reliable work done right for every yard.</p></div>

<!-- GALLERY -->
<div class="abs gallery-head"><span class="sq"></span><div><small>Our</small><h2>TOMLET BUILDERS GALLERY</h2></div></div>
<svg class="abs" style="left:972px;top:2276px" width="60" height="26" viewBox="0 0 60 26"><polygon points="20,2 20,24 2,13" fill="#8cb512"/><polygon points="38,2 38,24 56,13" fill="#222"/></svg>
<div class="photo" style="left:172px;top:2372px;width:290px;height:410px;background:linear-gradient(180deg,#9aa39c 0%,#6d8a4a 45%,#5c7d2e 100%)" role="img" aria-label="Photo of fresh turf being laid by gloved hands"></div>
<div class="photo" style="left:480px;top:2372px;width:296px;height:410px;background:linear-gradient(180deg,#7a6a58 0%,#a59b8f 45%,#8d8479 100%)" role="img" aria-label="Photo of concrete being poured from a chute"></div>
<div class="photo" style="left:790px;top:2372px;width:240px;height:200px;background:linear-gradient(180deg,#5b7f3a 0%,#8b9a6e 55%,#b2a998 100%)" role="img" aria-label="Photo of stone garden steps between plants"></div>
<div class="photo" style="left:790px;top:2588px;width:240px;height:194px;background:linear-gradient(180deg,#4f7a2e 0%,#7ea23f 55%,#b9b4a6 100%)" role="img" aria-label="Photo of a lawn with a paved stepping stone path"></div>

<!-- FEATURES -->
<div class="abs features"></div>
<div class="abs features-head"><small>Our</small><h2>TOMLET BUILDERS FEATURES</h2></div>
<div class="abs card plain" style="left:172px;top:3072px"><h4>SED UT PERSPICIATIS</h4><p>Quality work and friendly service on every job.</p></div>
<div class="abs card green" style="left:610px;top:3072px;padding-top:22px"><div class="card-icon"></div><h4>SED UT PERSPICIATIS</h4><p>Quality work and friendly service on every job.</p></div>
<div class="abs card green" style="left:172px;top:3312px;padding-top:22px"><div class="card-icon"></div><h4>SED UT PERSPICIATIS</h4><p>Quality work and friendly service on every job.</p></div>
<div class="abs card plain" style="left:610px;top:3312px;padding-top:22px"><div class="card-icon" style="color:#8cb512"></div><h4>SED UT PERSPICIATIS</h4><p>Quality work and friendly service on every job.</p></div>

<!-- FOOTER -->
<svg class="abs footer" viewBox="0 0 1200 596" preserveAspectRatio="none">
  <polygon points="0,0 600,90 1200,0 1200,596 0,596" fill="#0d0d0d"/>
</svg>
<div class="abs footer-brand"><span class="brand-mark"></span><span class="brand">TOMLET<br>BUILDERS</span></div>
<div class="abs footer-col" style="left:460px">
  <h3>QUICK LINKS</h3>
  <ul><li>Home</li><li>About us</li><li>Services</li><li>Projects/ Portfolio</li><li>Contact us</li></ul>
</div>
<div class="abs footer-col" style="left:740px">
  <h3>CONTACT US</h3>
  <div class="footer-contact"><span class="icon-circle"><svg width="18" height="18" viewBox="0 0 24 24"><path fill="#fff" d="M6.6 10.8a15 15 0 0 0 6.6 6.6l2.2-2.2c.3-.3.7-.4 1-.2 1.1.4 2.3.6 3.6.6.6 0 1 .4 1 1V20c0 .6-.4 1-1 1A17 17 0 0 1 3 4c0-.6.4-1 1-1h3.5c.6 0 1 .4 1 1 0 1.3.2 2.5.6 3.6.1.3 0 .7-.2 1z"/></svg></span><span>Call Us At:<br><b>+1 555 014 2290</b></span></div>
  <div class="footer-contact"><span class="icon-circle"><svg width="18" height="18" viewBox="0 0 24 24"><path fill="#fff" d="M3 5h18v14H3z"/><path fill="none" stroke="#8cb512" stroke-width="2" d="M3 6l9 7 9-7"/></svg></span><span>Email Us At:<br><b>info@tomletbuilders.com</b></span></div>
</div>
<div class="abs footer-rule"></div>
<div class="abs copyright">Copyrights © 2020 Tomlet Builders. All Rights Reserved.</div>

</body>
</html>
```